Cat-products company needs smart, yet endearing, business card

We need a business card design for a new, but up-and-running, business based in Honolulu, Hawaii. The business is Purrnest Nook Co. Our first product is the most environmentally-friendly cat grass kit ever seen on the planet. Future products, currently in the R&D phase, will include a variety of exciting cat scratchers. We also do consulting work to help apartment-dwellers make their home more cat-friendly and, in the future, plan on doing full, custom installs of structure to create high walkways for cats.

Target Market(s)

Middle-aged, apartment-dwelling, middle-class workers who own 1 or more cats and who dote on them.

Industry/Entity Type

Pet Care

Contact Information for Business Card

A striking, professional, yet warm and friendly design is what we're after.

Font styles to use
Serif
Sans Serif
Other font styles liked:
• Comfortaa

Colors

Designer to choose colors to be used in the design.

Requirements
Must have
• The company logo: (see attachment)
• The company name: Purrnest Nook Co
• The web address: www.purrnestnookco.com
• Email: support@purrnestnookco.com
• Phone: +1 (808) 571 6023
• Update (Fri Jun 30 3017 7:45pm Hawaii Time) I would like, is possible, uploaded picture of the cat grass kit on the back of the card with some text along the lines of: Purrnest Nook Co - Maker Of The Leafiest Feline Sprout Set Yet
Nice to have
• A cat picture, cartoon, real or silhouette that illustrates cats in action and/or relaxing; ie using the apartment space to live, play and relax in and being well-contented.
• Most of the website is done in the font: Comfortaa. It might be nice to continue using this for brand consistency.
Should not have
• Hard-to-read fonts.

```html
<!DOCTYPE html>
<html lang="en">
<head>
<meta charset="utf-8">
<title>Purrnest Nook Co — Business Card</title>
<link rel="stylesheet" href="https://fonts.googleapis.com/css2?family=Questrial&family=Roboto:wght@400&display=swap">
<style>
  :root {
    --backdrop: #e3e3e3;
    --card: #f5f5f4;
    --brown: #4e2c24;
    --gold: #f0a500;
    --text-grey: #555555;
    --rule: #4a4a4a;
    --paw-tint: #f7e6bf;
    --dot-1: #c9c9c9;
    --dot-2: #b5b5b5;
    --dot-3: #a3a3a3;
    --dot-4: #8f8f8f;
  }
  * { box-sizing: border-box; margin: 0; padding: 0; }
  html, body {
    width: 1200px; height: 960px; overflow: hidden;
    background: var(--backdrop);
    font-family: "Questrial", "Century Gothic", sans-serif;
  }
  .canvas { position: relative; width: 1200px; height: 960px; }

  .card {
    position: absolute; width: 600px; height: 343px;
    background: var(--card); border-radius: 18px;
  }
  .card--front { left: 314px; top: 113px; overflow: hidden; }
  .card--back { left: 311px; top: 472px; height: 342px; }

  .front__accent {
    position: absolute; left: 326px; top: 156px;
    width: 220px; height: 220px; border-radius: 50%;
    background: var(--paw-tint); opacity: .55;
  }

  .brand {
    position: absolute; left: 33px; top: 96px;
    display: flex; align-items: center; gap: 10px;
  }
  .brand__mark { width: 30px; height: 30px; background: var(--brown); border-radius: 4px; }
  .brand__name { font-size: 27px; color: var(--brown); line-height: 1.1; width: 150px; }

  .person { position: absolute; left: 335px; top: 138px; }
  .person__name {
    font-size: 22px; font-weight: 700; color: var(--brown);
    letter-spacing: .01em; -webkit-text-stroke: .4px var(--brown);
  }
  .person__role { font-size: 15px; color: var(--gold); margin-top: 2px; }

  .front__rule {
    position: absolute; left: 33px; top: 191px; width: 534px;
    height: 1px; background: var(--rule);
  }

  .address {
    position: absolute; left: 33px; top: 276px;
    font-size: 15px; color: var(--text-grey); line-height: 19px; font-style: normal;
  }

  .contact { position: absolute; left: 335px; top: 256px; list-style: none; }
  .contact__item {
    display: flex; align-items: center; gap: 8px;
    font-size: 15px; color: var(--text-grey); height: 19px;
  }
  .contact__icon { width: 13px; height: 13px; fill: var(--brown); flex: none; }

  .social { position: absolute; right: 16px; top: 18px; display: flex; gap: 2px; }
  .social__dot { width: 23px; height: 23px; border-radius: 50%; }
  .social__dot:nth-child(1) { background: var(--dot-1); }
  .social__dot:nth-child(2) { background: var(--dot-2); }
  .social__dot:nth-child(3) { background: var(--dot-3); }
  .social__dot:nth-child(4) { background: var(--dot-4); }

  .portrait {
    position: absolute; left: 214px; top: 71px;
    width: 172px; height: 200px; border-radius: 50%;
    border: 1px solid #222;
    background: radial-gradient(ellipse at 50% 40%, #1d1b1c 0%, #2a2424 42%, #9a5a3a 70%, #c98a5a 100%);
  }

  .back__url {
    position: absolute; left: 0; right: 0; top: 294px; text-align: center;
    font-family: "Roboto", sans-serif; font-size: 14px;
    letter-spacing: .36em; color: var(--text-grey);
  }
</style>
</head>
<body>
<main class="canvas">
  <section class="card card--front" aria-label="Card front">
    <div class="front__accent" aria-hidden="true"></div>
    <div class="brand">
      <span class="brand__mark" aria-hidden="true"></span>
      <span class="brand__name">Purrnest Nook Co</span>
    </div>
    <div class="person">
      <p class="person__name">KEONI HALE</p>
      <p class="person__role">CEO/FOUNDER</p>
    </div>
    <div class="front__rule"></div>
    <address class="address">4120 Mango Grove Lane<br>Honolulu, Hawaii 96822</address>
    <ul class="contact">
      <li class="contact__item">
        <svg class="contact__icon" viewBox="0 0 16 16"><path d="M3.5 1l2.5 3-1.5 2c1 2 3 4 5 5l2-1.5 3 2.5-1.5 2.5C8 15 1 8 1 2.5z"/></svg>
        +1 (808) 571 6023
      </li>
      <li class="contact__item">
        <svg class="contact__icon" viewBox="0 0 16 16"><path d="M1 3h14v1.2L8 9 1 4.2z M1 5.8l7 4.8 7-4.8V13H1z"/></svg>
        support@purrnestnookco.com
      </li>
      <li class="contact__item">
        <svg class="contact__icon" viewBox="0 0 16 16"><circle cx="8" cy="8" r="7"/><path d="M1 8h14M8 1c-3 3-3 11 0 14M8 1c3 3 3 11 0 14" stroke="#f5f5f4" stroke-width="1.2" fill="none"/></svg>
        www.purrnestnookco.com
      </li>
    </ul>
  </section>

  <section class="card card--back" aria-label="Card back">
    <div class="social" aria-hidden="true">
      <span class="social__dot"></span><span class="social__dot"></span>
      <span class="social__dot"></span><span class="social__dot"></span>
    </div>
    <div class="portrait" role="img" aria-label="Photo of a black cat asleep on a patterned cushion"></div>
    <p class="back__url">www.purrnestnookco.com</p>
  </section>
</main>
</body>
</html>
```